Calloway needs a modernized design

We would like a modern update (that can be responsive) to our existing website. Attached are the two existing pages we would like new concepts of - our home page and a page about one of our locations.

Calloway is provides executive offices and virtual office services. Startups, law firms, and financial services are our primary clients. We would like a professional, clean design, leaning towards minimalist. We intend to greatly reduce/eliminate the long paragraphs of text.

Requirements
Must have
• A design that can be responsive
Nice to have
• Large image(s) on home page that rotate.

```html
<!DOCTYPE html>
<html lang="en">
<head>
<meta charset="utf-8">
<title>Calloway Business Centers</title>
<link href="https://fonts.googleapis.com/css2?family=Cinzel:wght@400;600;700&family=Lato:wght@400;700&display=swap" rel="stylesheet">
<style>
:root{
  --navy:#263a6b;
  --navy-deep:#1f315c;
  --orange:#f7941d;
  --orange-deep:#ee8612;
  --ink:#333a44;
  --muted:#555b66;
  --paper:#ffffff;
  --mist:#eeeeee;
  --rule:#c9ced8;
  --btn-blue:#3d5c9f;
}
*{box-sizing:border-box;margin:0;padding:0}
html,body{width:1200px;height:2769px;overflow:hidden}
body{position:relative;background:var(--paper);font-family:'Lato',sans-serif;color:var(--ink)}
.abs{position:absolute}
.serif{font-family:'Cinzel',serif}

/* header */
.site-header{position:absolute;left:0;top:0;width:1200px;height:111px;background:var(--paper)}
.brand{position:absolute;left:61px;top:18px;display:flex;align-items:center;gap:12px}
.brand-dot{width:78px;height:78px;border-radius:50%;background:var(--navy)}
.brand-name{font-family:'Cinzel',serif;color:var(--navy);font-weight:700;font-size:34px;line-height:1}
.brand-sub{font-family:'Cinzel',serif;color:var(--navy);font-weight:700;font-size:15px;letter-spacing:.5px;margin-top:4px;border-top:2px solid var(--navy);padding-top:3px}
.top-tab{position:absolute;right:0;top:0;width:245px;height:34px;background:var(--navy);border-bottom-left-radius:22px;color:#fff;font-size:17px;display:flex;align-items:center;padding-left:34px;gap:10px}
.social-top{position:absolute;left:826px;top:9px;display:flex;gap:6px}
.social-top span{width:24px;height:24px;border-radius:50%}
.main-nav{position:absolute;left:470px;top:64px;display:flex;align-items:center;font-family:'Cinzel',serif;font-size:16px;font-weight:600;color:var(--navy);letter-spacing:.5px}
.main-nav a{color:inherit;text-decoration:none;padding:0 14px;border-left:1px solid var(--rule);line-height:16px}
.main-nav a.home{border:none;padding:0 14px 0 0}

/* hero */
.hero{position:absolute;left:0;top:111px;width:1200px;height:507px;background:linear-gradient(100deg,#e9edf1 0%,#f7f8fa 30%,#cfd8e2 55%,#b9c4d0 75%,#dfe4ea 100%)}
.hero-badge{position:absolute;left:812px;top:138px;width:314px;height:314px;border-radius:50%;background:rgba(30,30,34,.82);border:6px solid rgba(255,255,255,.35);display:flex;flex-direction:column;align-items:center;justify-content:center;color:#fff;text-align:center}
.hero-badge .mark{width:72px;height:72px;border-radius:50%;background:rgba(255,255,255,.25);margin-bottom:18px}
.hero-badge h2{font-family:'Lato',sans-serif;font-weight:700;font-size:25px;line-height:31px}
.hero-dots{display:flex;gap:5px;margin-top:12px}
.hero-dots i{width:9px;height:9px;border-radius:50%;background:#c9a14a}
.hero-dots i+i{background:#999}
.hero-arrow{position:absolute;top:243px;width:22px;height:44px;background:#222;color:#fff;display:flex;align-items:center;justify-content:center}

/* section headings */
.sec-title{font-family:'Cinzel',serif;color:var(--navy);font-weight:600;letter-spacing:1px}
.divider{position:absolute;height:1px;background:var(--rule)}
.divider-dot{position:absolute;width:22px;height:22px;border-radius:50%;background:var(--navy)}

.welcome-lead{position:absolute;left:90px;top:754px;width:1020px;text-align:center;color:var(--navy);font-weight:700;font-size:18px;line-height:27px}
.welcome-copy{position:absolute;left:90px;top:822px;width:1020px;text-align:center;color:var(--muted);font-size:14px;line-height:23px}
.pill{position:absolute;height:30px;border-radius:15px;display:flex;align-items:center;gap:8px;padding:0 12px 0 4px;font-size:14px;font-weight:700;color:#fff}
.pill .pd{width:22px;height:22px;border-radius:50%;background:var(--navy)}
.pill.orange{background:var(--orange)}
.pill.navy{background:var(--navy)}
.pill.navy .pd{background:#fff}
.pill.orange .pd{background:var(--navy)}

/* split offer */
.offer{position:absolute;top:1006px;height:466px;width:600px}
.offer.exec{left:0;background:linear-gradient(135deg,#2d4277,#24386a 60%,#1f3260)}
.offer.virtual{left:600px;background:linear-gradient(135deg,#f69a2a,#f59020 60%,#ef8716)}
.offer-title{position:absolute;top:1206px;width:600px;text-align:center;font-family:'Cinzel',serif;font-size:30px;letter-spacing:1px}
.offer-list{position:absolute;list-style:none;font-size:14px;font-weight:700;color:#fff}
.offer-list li{height:30px;display:flex;align-items:center;gap:8px}
.tick{width:14px;height:14px;border-radius:50%;background:var(--orange);display:inline-flex;align-items:center;justify-content:center}
.virtual-tick{background:var(--navy)}

/* community + services */
.community{position:absolute;left:0;top:1472px;width:595px;height:553px;background:linear-gradient(90deg,#f6f6f6,#e9e9e9)}
.services{position:absolute;left:595px;top:1472px;width:605px;height:553px;background:var(--mist)}
.photo{position:absolute;left:61px;top:1602px;width:489px;height:202px;background:linear-gradient(135deg,#6a4a34,#b98a62 45%,#8a6a52)}
.community-copy{position:absolute;left:61px;top:1816px;width:500px;font-size:13px;line-height:20.5px;color:#222}
.read{position:absolute;font-size:14px;font-weight:700;color:var(--navy)}
.service{position:absolute;left:640px;width:500px;height:136px;border-bottom:1px dashed #9aa0aa}
.service .ic{position:absolute;left:0;top:10px;width:60px;height:60px;border-radius:50%;background:#2b2b2b;border:3px solid #fff;box-shadow:0 0 0 1px #999}
.service h3{position:absolute;left:76px;top:0;font-size:20px;color:var(--orange);font-weight:700}
.service p{position:absolute;left:76px;top:32px;width:420px;font-size:13px;line-height:20px;color:#222}
.service .read{left:76px;top:80px}

/* partners */
.partner{position:absolute;top:2197px;width:157px;height:70px;border:1px solid #ccc;background:#fff;display:flex;align-items:center;justify-content:center}
.partner span{width:90px;height:22px;border-radius:4px;background:#cfd2d7}

/* footer */
.foot-h{position:absolute;top:2465px;font-family:'Cinzel',serif;color:#fff;font-size:19px;letter-spacing:1px}
.foot-line{position:absolute;top:2498px;height:1px;background:rgba(255,255,255,.25)}
.quick-links{position:absolute;left:61px;top:2516px;list-style:none;color:#fff;font-size:13px}
.quick-links li{height:35px;display:flex;align-items:center;gap:10px}
.quick-links li::before{content:"";width:5px;height:5px;border-radius:50%;background:var(--orange)}
.contact{position:absolute;left:310px;color:#fff;font-size:13px;line-height:20px;display:flex;gap:10px}
.field{position:absolute;left:646px;width:277px;background:#fff;border-radius:2px;font-size:13px;color:#888;padding:0 10px;display:flex;align-items:center}
.submit{position:absolute;left:646px;top:2656px;width:128px;height:36px;background:var(--btn-blue);color:#fff;font-weight:700;font-size:16px;display:flex;align-items:center;justify-content:center}
.follow{position:absolute;left:1018px;color:#fff;font-size:13px;font-weight:700;display:flex;align-items:center;gap:12px;letter-spacing:.5px}
.follow i{width:32px;height:32px;border-radius:50%}
.copyright{position:absolute;left:0;top:2723px;width:1200px;height:46px;background:var(--orange);color:#fff;font-size:13px;font-weight:700;display:flex;align-items:center;justify-content:center}
</style>
</head>
<body>

<header class="site-header">
  <div class="brand">
    <div class="brand-dot"></div>
    <div><div class="brand-name">CALLOWAY</div><div class="brand-sub">BUSINESS CENTERS</div></div>
  </div>
  <div class="social-top"><span style="background:#d3272b"></span><span style="background:#1a6fb4"></span><span style="background:#2ba6df"></span><span style="background:#dd4b39"></span></div>
  <div class="top-tab">
    <svg width="18" height="18" viewBox="0 0 24 24"><circle cx="12" cy="12" r="11" fill="none" stroke="#fff" stroke-width="2"/><path d="M8 6l2 0 1 3-1.5 1.2a8 8 0 0 0 4.3 4.3L15 13l3 1v2c0 1-1 2-2 2A11 11 0 0 1 6 8c0-1 1-2 2-2z" fill="#fff"/></svg>
    + 214.555.0148
  </div>
  <nav class="main-nav">
    <a class="home"><svg width="26" height="24" viewBox="0 0 26 24"><path d="M13 2L2 12h3v10h6v-6h4v6h6V12h3z" fill="#263a6b"/></svg></a>
    <a>Properties</a><a>Virtual Tours &amp; Videos</a><a>Photos</a><a>Broker Referrals</a>
  </nav>
</header>

<section class="hero" role="img" aria-label="Businessman presenting a chart on a flip board to seated colleagues in a bright office">
  <div class="hero-arrow" style="left:0;border-radius:0 22px 22px 0">‹</div>
  <div class="hero-arrow" style="right:0;border-radius:22px 0 0 22px">›</div>
</section>
<div class="hero-badge">
  <div class="mark"></div>
  <h2>We Provide Executive<br>Offices And Virtual<br>Office Services</h2>
  <div class="hero-dots"><i></i><i></i><i></i></div>
</div>

<section class="welcome">
  <h1 class="sec-title abs" style="left:0;top:652px;width:1200px;text-align:center;font-size:38px">WELCOME TO CALLOWAY BUSINESS CENTERS</h1>
  <div class="divider" style="left:290px;top:720px;width:620px"></div>
  <div class="divider-dot" style="left:589px;top:709px"></div>
  <p class="welcome-lead">Come See Why Smarter Companies are Choosing Calloway Business Centers' Dallas, Ft. Worth and Houston Executive Office Suites, Virtual Offices, Meeting Rooms and Video Conferencing.</p>
  <p class="welcome-copy">Either you need Dallas/Ft. Worth Office Space, Dallas Executive Suites, Ft. Worth Executive Suites, Houston Office Space, Houston Executive Suites, or maybe you simply need a place to stop in and use an on-demand office or meeting room from time to time or utilize our local business phone numbers, phone answering or business addresses through one of our virtual office solutions</p>
  <div class="pill orange" style="left:530px;top:922px">
    <span class="pd"></span>Read More »
  </div>
</section>

<section>
  <div class="offer exec" role="img" aria-label="Faded office workspace photo under navy tint"></div>
  <div class="offer virtual" role="img" aria-label="Faded office workspace photo under orange tint"></div>
  <svg class="abs" style="left:0;top:1006px" width="1200" height="466">
    <polygon points="570,0 630,0 600,20" fill="#fff"/>
    <line x1="308" y1="124" x2="905" y2="124" stroke="#c8cbd3" stroke-width="2"/>
    <circle cx="398" cy="124" r="5" fill="#c8cbd3"/><circle cx="816" cy="124" r="5" fill="#c8cbd3"/>
    <circle cx="308" cy="124" r="66" fill="#f7941d" stroke="#fff" stroke-width="3"/>
    <circle cx="905" cy="124" r="66" fill="#263a6b" stroke="#fff" stroke-width="3"/>
    <circle cx="600" cy="124" r="38" fill="#fff" stroke="#263a6b" stroke-width="4"/>
    <circle cx="600" cy="124" r="24" fill="#263a6b"/>
    <g fill="none" stroke="#fff" stroke-width="4" stroke-linecap="round">
      <rect x="292" y="88" width="32" height="30" rx="8" fill="#fff"/>
      <rect x="284" y="120" width="48" height="9" rx="4" fill="#fff"/>
      <line x1="308" y1="130" x2="308" y2="148"/><line x1="294" y1="152" x2="322" y2="152"/>
      <line x1="278" y1="112" x2="278" y2="126"/><line x1="338" y1="112" x2="338" y2="126"/>
    </g>
    <g fill="#fff">
      <circle cx="893" cy="98" r="9"/>
      <rect x="882" y="110" width="20" height="26" rx="5"/>
      <rect x="908" y="92" width="22" height="30" rx="2"/>
      <rect x="872" y="138" width="66" height="5"/>
      <rect x="878" y="143" width="4" height="16"/><rect x="928" y="143" width="4" height="16"/>
    </g>
  </svg>
  <h2 class="offer-title" style="left:0;color:var(--orange);font-variant:small-caps">Executive Offices</h2>
  <h2 class="offer-title" style="left:600px;color:#fff">VIRTUAL OFFICE</h2>

  <ul class="offer-list" style="left:111px;top:1268px">
    <li><span class="tick"><svg width="9" height="9" viewBox="0 0 10 10"><path d="M1 5l3 3 5-6" stroke="#fff" stroke-width="2" fill="none"/></svg></span>Full Service Offices</li>
    <li><span class="tick"><svg width="9" height="9" viewBox="0 0 10 10"><path d="M1 5l3 3 5-6" stroke="#fff" stroke-width="2" fill="none"/></svg></span>Disaster Recovery</li>
    <li><span class="tick"><svg width="9" height="9" viewBox="0 0 10 10"><path d="M1 5l3 3 5-6" stroke="#fff" stroke-width="2" fill="none"/></svg></span>All-Inclusive Pricing!</li>
  </ul>
  <ul class="offer-list" style="left:295px;top:1268px">
    <li><span class="tick"><svg width="9" height="9" viewBox="0 0 10 10"><path d="M1 5l3 3 5-6" stroke="#fff" stroke-width="2" fill="none"/></svg></span>Flexible Contracts from $395</li>
    <li><span class="tick"><svg width="9" height="9" viewBox="0 0 10 10"><path d="M1 5l3 3 5-6" stroke="#fff" stroke-width="2" fill="none"/></svg></span>Corporate or Satellite Offices</li>
  </ul>
  <ul class="offer-list" style="left:707px;top:1268px">
    <li><span class="tick virtual-tick"><svg width="9" height="9" viewBox="0 0 10 10"><path d="M1 5l3 3 5-6" stroke="#fff" stroke-width="2" fill="none"/></svg></span>Mailing Address $49/mo</li>
    <li><span class="tick virtual-tick"><svg width="9" height="9" viewBox="0 0 10 10"><path d="M1 5l3 3 5-6" stroke="#fff" stroke-width="2" fill="none"/></svg></span>Local Phone &amp; Mail $99/mo</li>
    <li><span class="tick virtual-tick"><svg width="9" height="9" viewBox="0 0 10 10"><path d="M1 5l3 3 5-6" stroke="#fff" stroke-width="2" fill="none"/></svg></span>Corporate or Satellite Offices</li>
  </ul>
  <ul class="offer-list" style="left:949px;top:1268px">
    <li><span class="tick virtual-tick"><svg width="9" height="9" viewBox="0 0 10 10"><path d="M1 5l3 3 5-6" stroke="#fff" stroke-width="2" fill="none"/></svg></span>Flexible Contracts</li>
    <li><span class="tick virtual-tick"><svg width="9" height="9" viewBox="0 0 10 10"><path d="M1 5l3 3 5-6" stroke="#fff" stroke-width="2" fill="none"/></svg></span>All-Inclusive Pricing!</li>
  </ul>
  <div class="pill orange" style="left:236px;top:1386px"><span class="pd"></span>Read More »</div>
  <div class="pill navy" style="left:834px;top:1386px"><span class="pd"></span>Read More »</div>
</section>

<section>
  <div class="community"></div>
  <div class="services"></div>
  <h2 class="sec-title abs" style="left:61px;top:1518px;font-size:36px">COMMUNITY</h2>
  <div class="photo" role="img" aria-label="Team members stacking their hands together over a wooden table"></div>
  <p class="community-copy">Lorem ipsum dolor sit amet, consectetuer adipiscing elit, sed diam nonummy nibh euismod tincidunt ut laoreet dolore magna aliquam erat volutpat. Ut wisi enim ad minim veniam, quis nostrud exerci tation ullamcorper suscipit lobortis nisl utiquip ex ea commodo consequat. Duis autem vel eum iriure dolor in hendrerit inputate velit esse molestie consequat, vel illum dolore eu feugiat nulla facilisis at vero eros et accumsan et iusto odio dignissim qui blandit</p>
  <div class="read" style="left:64px;top:1956px">Read More »</div>

  <h2 class="sec-title abs" style="left:640px;top:1520px;font-size:32px">OTHER SERVICES</h2>
  <div class="divider" style="left:640px;top:1572px;width:500px;background:#d6d8dc"></div>
  <div class="service" style="top:1596px"><div class="ic"></div><h3>On-demand Meeting Rooms</h3><p>Lorem ipsum dolor sit amet, consectetuer adipiscing elit, sed diam my nibh euismod dloer sknev cjsrewvc bnarv bdivrt.</p><div class="read">Read More »</div></div>
  <div class="service" style="top:1733px"><div class="ic"></div><h3>On-demand Training Rooms</h3><p>Lorem ipsum dolor sit amet, consectetuer adipiscing elit, sed diam my nibh euismod dloer sknev cjsrewvc bnarv bdivrt.</p><div class="read">Read More »</div></div>
  <div class="service" style="top:1870px;border:none"><div class="ic"></div><h3>Virtual Office Solutions</h3><p>Lorem ipsum dolor sit amet, consectetuer adipiscing elit, sed diam my nibh euismod dloer sknev cjsrewvc bnarv bdivrt.</p><div class="read">Read More »</div></div>
</section>

<section>
  <h2 class="sec-title abs" style="left:0;top:2076px;width:1200px;text-align:center;font-size:36px">OUR PARTNERS</h2>
  <div class="divider" style="left:290px;top:2138px;width:620px"></div>
  <div class="divider-dot" style="left:589px;top:2127px"></div>
  <svg class="abs" style="left:16px;top:2208px" width="24" height="48"><path d="M20 2L4 24l16 22" stroke="#c8cbd3" stroke-width="3" fill="none"/></svg>
  <svg class="abs" style="left:1162px;top:2208px" width="24" height="48"><path d="M4 2l16 22L4 46" stroke="#c8cbd3" stroke-width="3" fill="none"/></svg>
  <div class="partner" style="left:61px"><span></span></div>
  <div class="partner" style="left:246px"><span></span></div>
  <div class="partner" style="left:430px"><span></span></div>
  <div class="partner" style="left:615px"><span></span></div>
  <div class="partner" style="left:800px"><span></span></div>
  <div class="partner" style="left:984px"><span></span></div>
</section>

<footer>
  <svg class="abs" style="left:0;top:2340px" width="1200" height="383">
    <path d="M0 80 Q600 -10 1200 80 L1200 383 L0 383Z" fill="#dfe2e8"/>
    <path d="M0 88 Q600 0 1200 88 L1200 383 L0 383Z" fill="#263a6b"/>
    <circle cx="600" cy="24" r="44" fill="#fff" stroke="#263a6b" stroke-width="5"/>
    <circle cx="600" cy="24" r="28" fill="#263a6b"/>
  </svg>
  <h3 class="foot-h" style="left:61px">QUICK LINKS</h3>
  <h3 class="foot-h" style="left:310px">CONTACT DETAILS</h3>
  <h3 class="foot-h" style="left:642px">QUICK CONTACT</h3>
  <h3 class="foot-h" style="left:1018px">FOLLOW US</h3>
  <div class="foot-line" style="left:61px;width:195px"></div>
  <div class="foot-line" style="left:310px;width:240px"></div>
  <div class="foot-line" style="left:642px;width:285px"></div>
  <div class="foot-line" style="left:1018px;width:130px"></div>

  <ul class="quick-links"><li>Home</li><li>Properties</li><li>Virtual Tours &amp; Videos</li><li>Photos</li><li>Broker Referrals</li></ul>

  <div class="contact" style="top:2518px"><svg width="14" height="18" viewBox="0 0 14 18"><path d="M7 0a7 7 0 0 1 7 7c0 5-7 11-7 11S0 12 0 7a7 7 0 0 1 7-7z" fill="#f7941d"/><circle cx="7" cy="7" r="2.5" fill="#263a6b"/></svg><div><b>CALLOWAY BUSINESS CENTERS</b><br>2150 Harwell Parkway<br>Suite 500 , Dallas, Texas 75206</div></div>
  <div class="contact" style="top:2600px"><svg width="14" height="14" viewBox="0 0 24 24"><path d="M5 2h4l2 5-2.5 2a12 12 0 0 0 6.5 6.5L17 13l5 2v4a3 3 0 0 1-3 3A19 19 0 0 1 2 5a3 3 0 0 1 3-3z" fill="#f7941d"/></svg>+ 214.555.0148</div>
  <div class="contact" style="top:2635px"><svg width="14" height="14" viewBox="0 0 24 24"><rect x="2" y="8" width="20" height="10" rx="2" fill="#f7941d"/><rect x="6" y="3" width="12" height="6" fill="#f7941d"/><rect x="6" y="15" width="12" height="6" fill="#fff"/></svg>+ 214.555.0148</div>
  <div class="contact" style="top:2670px"><svg width="14" height="12" viewBox="0 0 24 18"><rect width="24" height="18" rx="2" fill="#f7941d"/><path d="M1 1l11 9 11-9" stroke="#263a6b" stroke-width="2" fill="none"/></svg>Offices@CallowayOffices.com</div>

  <div class="field" style="top:2522px;height:37px">Name</div>
  <div class="field" style="top:2567px;height:37px">Email</div>
  <div class="field" style="top:2612px;height:37px">Message</div>
  <div class="submit">Submit</div>

  <div class="follow" style="top:2526px"><i style="background:#dd4b39"></i>CIRCLECAST</div>
  <div class="follow" style="top:2571px"><i style="background:#2ba6df"></i>CHIRPLINE</div>
  <div class="follow" style="top:2616px"><i style="background:#1a6fb4"></i>LINKWORK</div>
  <div class="follow" style="top:2661px"><i style="background:#d3272b"></i>PINBOARDLY</div>

  <div class="copyright">Copyright © 2016 &nbsp;Calloway Business Centers. All Rights Reserved.</div>
</footer>

</body>
</html>
```